New Website

New website is to be the same as Amber Lantern.

Website needs to be fully functional, with only text and logo to be added by client at a later date.

Logo has been added for reference.

```html
<!DOCTYPE html>
<html lang="en">
<head>
<meta charset="utf-8">
<title>Velora – Avenues for business growth</title>
<link rel="stylesheet" href="https://fonts.googleapis.com/css2?family=Open+Sans:ital,wght@0,300;0,400;0,600;0,700;1,400&display=swap">
<style>
:root{
  --brand:#3b4a9b;
  --brand-dark:#2e3b82;
  --brand-deep:#26336f;
  --ink:#444;
  --muted:#666;
  --line:#dcdcdc;
  --soft:#f0f0f0;
  --white:#fff;
  --accent:#d33a2c;
}
*{box-sizing:border-box;margin:0;padding:0}
html,body{width:1200px;height:2917px;overflow:hidden}
body{font-family:"Open Sans",Arial,sans-serif;color:var(--ink);background:var(--white);position:relative}
.abs{position:absolute}

/* header */
.site-header{position:absolute;left:0;top:0;width:1200px;height:86px;background:#fafafa;border-bottom:4px solid var(--brand)}
.brand{position:absolute;display:flex;align-items:center;gap:12px}
.brand-mark{width:54px;height:54px;border-radius:50%;background:var(--brand)}
.brand-name{font-weight:400;color:var(--brand);font-size:32px;letter-spacing:1px;line-height:1}
.brand-tag{font-size:10px;color:var(--brand);margin-top:4px}
.site-header .brand{left:111px;top:14px}
.main-nav{position:absolute;left:403px;top:0;display:flex;height:82px}
.main-nav a{display:block;height:82px;border-left:1px solid var(--line);padding:24px 0 0 18px;text-decoration:none}
.main-nav a:last-child{border-right:1px solid var(--line)}
.main-nav .nav-title{display:block;font-size:13px;color:var(--brand);text-transform:uppercase}
.main-nav .nav-sub{display:block;font-size:12px;color:var(--muted);margin-top:2px}

/* hero */
.hero{position:absolute;left:0;top:86px;width:1200px;height:445px;background:linear-gradient(160deg,#1d3f7c 0%,#3f79bf 40%,#8fb8e2 65%,#2a5596 100%)}
.hero-text{position:absolute;left:628px;top:100px;color:var(--white)}
.hero-title{font-size:46px;font-weight:600;line-height:1.1}
.hero-sub{font-size:37px;font-weight:300;line-height:1.2}

/* intro */
.intro{position:absolute;left:0;top:531px;width:1200px;height:257px;text-align:center}
.intro .brand{left:486px;top:45px}
.intro .brand-mark{width:68px;height:68px}
.intro .brand-name{font-size:34px}
.intro-copy{position:absolute;left:140px;top:138px;width:930px;font-size:12.5px;line-height:24px;color:var(--muted)}

/* how it works */
.how{position:absolute;left:0;top:788px;width:1200px;height:500px;background:var(--soft);text-align:center}
.section-title{font-size:20px;font-weight:700;color:var(--brand);text-transform:uppercase}
.how .section-title{position:absolute;left:0;right:0;top:42px}
.how-sub{position:absolute;left:0;right:0;top:80px;font-size:17px;color:var(--muted)}
.step{position:absolute;top:140px;width:222px;height:225px;background:#fafafa;border-bottom:4px solid #e2e2e2;box-shadow:0 1px 2px rgba(0,0,0,.05)}
.step.is-active{border-bottom-color:var(--brand)}
.step svg{position:absolute;left:88px;top:28px}
.step-kicker{position:absolute;left:0;right:0;top:104px;font-size:16px;color:#888;text-transform:uppercase}
.step-title{position:absolute;left:0;right:0;top:126px;font-size:18px;font-weight:700;color:var(--brand);text-transform:uppercase}
.step-copy{position:absolute;left:30px;right:30px;top:156px;font-size:12.5px;line-height:22px;color:var(--muted)}
.btn{position:absolute;left:500px;top:408px;width:200px;height:46px;background:var(--brand);color:var(--white);font-size:13px;font-weight:600;line-height:46px;text-transform:uppercase;border-radius:2px}

/* testimonials */
.clients{position:absolute;left:0;top:1288px;width:1200px;height:466px;text-align:center}
.clients .section-title{position:absolute;left:0;right:0;top:62px}
.client{position:absolute;top:120px;width:230px}
.client-photo{width:230px;height:224px}
.quote-card{width:230px;height:224px;background:var(--brand);color:var(--white);text-align:left;padding:38px 36px;font-size:13px;line-height:24px;position:relative}
.quote-card .q{position:absolute;font-size:30px;font-family:Georgia,serif;line-height:1}
.client-name{margin-top:20px;font-size:13px;font-weight:700;color:var(--brand);text-transform:uppercase}
.client-role{font-size:13px;color:var(--muted);margin-top:4px}
.chev{position:absolute;top:232px;color:#ccc;font-size:26px;font-weight:300}

/* video */
.video-block{position:absolute;left:99px;top:1754px;width:1002px;height:380px}
.video-frame{position:absolute;left:0;top:0;width:650px;height:380px;background:linear-gradient(120deg,#c5ccd4,#7a8795 50%,#3b4552)}
.video-controls{position:absolute;left:0;bottom:0;width:650px;height:43px;background:#1e1e1e}
.video-info{position:absolute;left:650px;top:0;width:352px;height:380px;background:var(--brand);color:var(--white);padding:60px 46px 0}
.video-info .brand{position:static}
.video-info .brand-mark{width:58px;height:58px;background:var(--white)}
.video-info .brand-name,.video-info .brand-tag{color:var(--white)}
.video-title{font-size:27px;font-weight:400;margin-top:22px}
.video-copy{font-size:12.5px;line-height:24px;margin-top:12px}

/* experts */
.experts{position:absolute;left:0;top:2192px;width:1200px;height:426px;background:linear-gradient(135deg,#d2d2d2,#f0f0f0 40%,#dcdcdc 70%,#efefef)}
.experts .section-title{position:absolute;left:0;right:0;top:52px;text-align:center}
.expert{position:absolute;top:117px;width:241px;height:243px}
.expert-photo{width:241px;height:175px}
.expert-label{position:relative;height:68px;background:var(--brand);color:var(--white);padding:14px 0 0 22px}
.expert-name{font-size:13px;font-weight:700;text-transform:uppercase}
.expert-role{font-size:13px;margin-top:3px}
.expert-label .more{position:absolute;right:0;top:0;width:40px;height:68px;border-left:1px solid rgba(255,255,255,.15)}

/* footer */
.site-footer{position:absolute;left:0;top:2618px;width:1200px;height:249px;background:var(--brand);color:var(--white)}
.foot-col{position:absolute;top:42px}
.foot-head{font-size:12.5px;font-weight:700;text-transform:uppercase;margin-bottom:16px}
.foot-col ul{list-style:none;font-size:11.5px;line-height:22.5px}
.news-title{font-size:11px;font-weight:600;text-transform:uppercase;margin-top:14px}
.news-date{font-size:11px;font-style:italic;margin-top:6px}
.news-copy{font-size:11px;line-height:23px;margin-top:6px;width:310px}
.social li{display:flex;align-items:center;gap:10px;height:34px}
.social .sq{width:24px;height:24px;border:1px solid rgba(255,255,255,.8)}
.bottom-bar{position:absolute;left:0;top:2867px;width:1200px;height:50px;background:var(--brand-deep);color:var(--white);font-size:11px;text-align:center;line-height:50px}
</style>
</head>
<body>

<header class="site-header">
  <div class="brand"><span class="brand-mark"></span><div><div class="brand-name">VELORA</div><div class="brand-tag">avenues for business growth</div></div></div>
  <nav class="main-nav">
    <a href="#" style="width:138px"><span class="nav-title">About</span><span class="nav-sub">Know our History</span></a>
    <a href="#" style="width:136px"><span class="nav-title">Services</span><span class="nav-sub">View our Services</span></a>
    <a href="#" style="width:140px"><span class="nav-title">How it works</span><span class="nav-sub">View info for work</span></a>
    <a href="#" style="width:142px"><span class="nav-title">Testimonials</span><span class="nav-sub">What our clien's says</span></a>
    <a href="#" style="width:140px"><span class="nav-title">Contact us</span><span class="nav-sub">Get in Touch</span></a>
  </nav>
</header>

<section class="hero" role="img" aria-label="Glass office towers rising into a blue sky">
  <div class="hero-text"><div class="hero-title">Velora</div><div class="hero-sub">Avenues for business growth</div></div>
</section>

<section class="intro">
  <div class="brand"><span class="brand-mark"></span><div><div class="brand-name">VELORA</div><div class="brand-tag">avenues for business growth</div></div></div>
  <p class="intro-copy">Lorem Ipsum is simply dummy text of the printing and typesetting industry. Lorem Ipsum has been the industry's standard dummy text ever since the 1500s, when an unknown printer took a galley of type and scrambled it to make a type specimen book. It has survived not only five centuries, but also the leap into electronic typesetting, remaining essentially unchanged. It was popularised in the 1960s with the release of Letterset sheets containing...</p>
</section>

<section class="how">
  <h2 class="section-title">How it works</h2>
  <p class="how-sub">Lorem Ipsum is simply dummy text of the printing and typesetting industry has been the industry's standard.</p>
  <div class="step is-active" style="left:99px">
    <svg width="46" height="46" viewBox="0 0 46 46" fill="none" stroke="#333" stroke-width="4" stroke-linecap="round"><path d="M20 14 L14 8 a6 6 0 0 0 -8 8 l6 6"/><path d="M26 32 l6 6 a6 6 0 0 0 8 -8 l-6 -6"/><path d="M16 30 L30 16"/><path d="M22 4v5M4 22h5M37 24h5M24 37v5" stroke-width="2.5"/></svg>
    <div class="step-kicker">Pre-session</div><div class="step-title">Discovery</div><p class="step-copy">Lorem Ipsum is simply dummy text of the printing.</p>
  </div>
  <div class="step" style="left:357px">
    <svg width="46" height="46" viewBox="0 0 46 46" fill="none" stroke="#333" stroke-width="4" stroke-linecap="round"><path d="M20 14 L14 8 a6 6 0 0 0 -8 8 l6 6"/><path d="M26 32 l6 6 a6 6 0 0 0 8 -8 l-6 -6"/><path d="M16 30 L30 16"/><path d="M22 4v5M4 22h5M37 24h5M24 37v5" stroke-width="2.5"/></svg>
    <div class="step-kicker">Pre-session</div><div class="step-title">Discovery</div><p class="step-copy">Lorem Ipsum is simply dummy text of the printing.</p>
  </div>
  <div class="step" style="left:615px">
    <svg width="46" height="46" viewBox="0 0 46 46" fill="none" stroke="#333" stroke-width="4" stroke-linecap="round"><path d="M20 14 L14 8 a6 6 0 0 0 -8 8 l6 6"/><path d="M26 32 l6 6 a6 6 0 0 0 8 -8 l-6 -6"/><path d="M16 30 L30 16"/><path d="M22 4v5M4 22h5M37 24h5M24 37v5" stroke-width="2.5"/></svg>
    <div class="step-kicker">Pre-session</div><div class="step-title">Discovery</div><p class="step-copy">Lorem Ipsum is simply dummy text of the printing.</p>
  </div>
  <div class="step" style="left:872px">
    <svg width="46" height="46" viewBox="0 0 46 46" fill="none" stroke="#333" stroke-width="4" stroke-linecap="round"><path d="M20 14 L14 8 a6 6 0 0 0 -8 8 l6 6"/><path d="M26 32 l6 6 a6 6 0 0 0 8 -8 l-6 -6"/><path d="M16 30 L30 16"/><path d="M22 4v5M4 22h5M37 24h5M24 37v5" stroke-width="2.5"/></svg>
    <div class="step-kicker">Pre-session</div><div class="step-title">Discovery</div><p class="step-copy">Lorem Ipsum is simply dummy text of the printing.</p>
  </div>
  <div class="btn">See how it works</div>
</section>

<section class="clients">
  <h2 class="section-title">What our clien's say</h2>
  <span class="chev" style="left:62px">‹</span><span class="chev" style="left:1126px">›</span>
  <div class="client" style="left:99px">
    <div class="quote-card"><span class="q" style="left:22px;top:32px">“</span>simply dummy text of the printing and typesetting industry. Lorem Ipsum has been the industry's standard dummy text ever since the 1500s<span class="q" style="right:22px;bottom:14px">”</span></div>
    <div class="client-name">Miles Carter</div><div class="client-role">Marketing Executive</div>
  </div>
  <div class="client" style="left:356px">
    <div class="client-photo" role="img" aria-label="Portrait of a smiling client at a laptop" style="background:linear-gradient(160deg,#e6e6e6,#a9b6c6 60%,#4f79b4)"></div>
    <div class="client-name">Miles Carter</div><div class="client-role">Marketing Executive</div>
  </div>
  <div class="client" style="left:615px">
    <div class="client-photo" role="img" aria-label="Portrait of a client in a blue shirt" style="background:linear-gradient(160deg,#ececec,#b9b2aa 55%,#5c7fae)"></div>
    <div class="client-name">Miles Carter</div><div class="client-role">Marketing Executive</div>
  </div>
  <div class="client" style="left:871px">
    <div class="client-photo" role="img" aria-label="Portrait of a client in a striped shirt" style="background:linear-gradient(160deg,#f1f1f1,#d2b9a8 55%,#c9c3d6)"></div>
    <div class="client-name">Miles Carter</div><div class="client-role">Marketing Executive</div>
  </div>
</section>

<section class="video-block">
  <div class="video-frame" role="img" aria-label="Video still of two businessmen talking at a meeting table">
    <svg class="abs" style="left:294px;top:154px" width="62" height="62" viewBox="0 0 62 62"><circle cx="31" cy="31" r="29" fill="none" stroke="#fff" stroke-width="3" opacity=".8"/><path d="M25 19 L44 31 L25 43Z" fill="#fff" opacity=".8"/></svg>
  </div>
  <div class="video-controls">
    <svg width="650" height="43" viewBox="0 0 650 43"><rect x="26" y="15" width="4" height="13" fill="#fff"/><rect x="34" y="15" width="4" height="13" fill="#fff"/><rect x="66" y="0" width="1" height="43" fill="#333"/><rect x="96" y="18" width="444" height="7" rx="3.5" fill="#111"/><rect x="96" y="18" width="110" height="7" rx="3.5" fill="var(--accent)"/><circle cx="180" cy="21.5" r="6" fill="#fff"/><path d="M564 17h4l6-5v19l-6-5h-4z" fill="#fff"/><path d="M578 16q4 5.5 0 11" stroke="#fff" fill="none" stroke-width="1.5"/><path d="M624 14h-6v2h4v4h2zM624 29h-6v-2h4v-4h2zM609 14h6v2h-4v4h-2zM609 29h6v-2h-4v-4h-2z" fill="#fff"/></svg>
  </div>
  <div class="video-info">
    <div class="brand"><span class="brand-mark"></span><div><div class="brand-name">VELORA</div><div class="brand-tag">avenues for business growth</div></div></div>
    <h2 class="video-title">OUR VIDEOS</h2>
    <p class="video-copy">Lorem Ipsum is simply dummy text of the printing and typesetting industry. Lorem Ipsum has been the industry's standard dummy text ever since the 1500s, when an unknown printer took a galley of type and scrambled...</p>
  </div>
</section>

<section class="experts">
  <h2 class="section-title">Introducing your business expert network</h2>
  <div class="expert" style="left:99px">
    <div class="expert-photo" role="img" aria-label="Portrait of a bearded expert in glasses" style="background:linear-gradient(160deg,#ececec,#8e8e8e 60%,#2b2b2b)"></div>
    <div class="expert-label"><div class="expert-name">Miles Carter</div><div class="expert-role">Marketing Executive</div><span class="more"></span></div>
  </div>
  <div class="expert" style="left:354px">
    <div class="expert-photo" role="img" aria-label="Portrait of a smiling expert" style="background:linear-gradient(160deg,#f4f1ec,#d9c3a8 55%,#7a92b6)"></div>
    <div class="expert-label"><div class="expert-name">Miles Carter</div><div class="expert-role">Marketing Executive</div><span class="more"></span></div>
  </div>
  <div class="expert" style="left:607px">
    <div class="expert-photo" role="img" aria-label="Portrait of a young expert against a stone wall" style="background:linear-gradient(160deg,#b7b39c,#8b8a74 55%,#3e4e6a)"></div>
    <div class="expert-label"><div class="expert-name">Miles Carter</div><div class="expert-role">Marketing Executive</div><span class="more"></span></div>
  </div>
  <div class="expert" style="left:860px">
    <div class="expert-photo" role="img" aria-label="Portrait of an expert on a phone call" style="background:linear-gradient(160deg,#cfd6de,#8393a6 55%,#2e3b52)"></div>
    <div class="expert-label"><div class="expert-name">Miles Carter</div><div class="expert-role">Marketing Executive</div><span class="more"></span></div>
  </div>
</section>

<footer class="site-footer">
  <div class="foot-col" style="left:103px">
    <div class="foot-head">Latest news <span style="position:absolute;left:290px;font-weight:400">‹ ›</span></div>
    <div class="news-title">Lorem ipsum is simply dummy text of the printing</div>
    <div class="news-date">Posted on 27 November 2014</div>
    <p class="news-copy">Lorem Ipsum is simply dummy text of the printing and typesetting industry. Lorem Ipsum has been the industry's standard dummy text ever since the 1500s...</p>
  </div>
  <div class="foot-col" style="left:515px">
    <div class="foot-head">Welcome</div>
    <ul><li>Home</li><li>About Us</li><li>Services</li><li>How it works</li><li>Testimonials</li><li>Contact us</li></ul>
  </div>
  <div class="foot-col" style="left:702px">
    <div class="foot-head">Information</div>
    <ul><li>Terms &amp; Conditions</li><li>Privacy Policy</li><li>Sitemap</li></ul>
  </div>
  <div class="foot-col" style="left:920px">
    <div class="foot-head">Follow us</div>
    <ul class="social"><li><span class="sq"></span>: Facepage</li><li><span class="sq"></span>: Chirper</li><li><span class="sq"></span>: Plusone</li><li><span class="sq"></span>: Linkwork</li></ul>
  </div>
</footer>
<div class="bottom-bar">© Velora 2015. All rights reserved.</div>

</body>
</html>
```